Presentation and Communication Coaching Services Business needs updated interactive web site

I want to keep the color scheme, functionality, and pages of my current site, but with a newer/updated look. I need to improve security and simplify images, etc. (Please see current site http://brightwellvoicetutor.com ) This will need be functional on mobile devices, as well.

I'm attached to the scrolling client list and scrolling client feedback.

Industry/Entity Type

Professional Service

Font styles to use
Sans Serif

Colors
0356a4
f37122
33a6d7

Requirements
Must have
• scrolling client banner on home page, client comments slider, color scheme
• Please see current site: http://brightwellvoicetutor.com
Nice to have
• better action/appearance
Should not have
• I don't want it to look like all the other sites/templates

```html
<!DOCTYPE html>
<html lang="en">
<head>
<meta charset="utf-8">
<title>Brightwell Voice Tutor</title>
<link href="https://fonts.googleapis.com/css2?family=Lato:ital,wght@0,300;0,400;0,700;0,900;1,400;1,900&display=swap" rel="stylesheet">
<style>
:root{
  --blue:#0356a4;
  --orange:#f37122;
  --sky:#33a6d7;
  --navy:#0b3d86;
  --dark:#1e1e1e;
  --ink:#333;
  --grey:#777;
  --pale:#f1f1f1;
}
*{margin:0;padding:0;box-sizing:border-box}
html,body{width:1200px;height:4775px;overflow:hidden}
body{font-family:'Lato',sans-serif;color:var(--ink);background:#fff;position:relative}
section,header,footer{position:absolute;left:0;width:1200px;overflow:hidden}
.btn{display:inline-block;background:var(--orange);color:#fff;font-weight:700;font-size:15px;border-radius:30px;padding:14px 32px;text-transform:uppercase;letter-spacing:.5px}
.ghost{position:absolute;font-weight:900;color:rgba(0,0,0,.06);font-size:120px;letter-spacing:2px;white-space:nowrap}
.rule{width:50px;height:3px;background:var(--orange);margin:14px auto 0}

/* header + hero */
.hero{top:0;height:780px;background:linear-gradient(180deg,#2a2f38 0%,#4a3f3a 45%,#23252b 100%)}
.hero-photo{position:absolute;inset:0;background:radial-gradient(ellipse at 50% 40%,rgba(200,140,90,.35),rgba(20,20,30,.6) 70%)}
.login{position:absolute;right:112px;top:30px;background:var(--orange);color:#fff;font-weight:700;font-size:14px;border-radius:24px;padding:11px 26px}
.brand{position:absolute;left:112px;top:96px;color:#fff;font-size:24px;font-weight:400}
.brand b{color:var(--orange);font-weight:400}
.nav{position:absolute;left:528px;top:104px;display:flex;gap:26px;color:#fff;font-size:13px;font-weight:700;text-transform:uppercase}
.nav .on{border-bottom:2px solid var(--orange);padding-bottom:4px}
.hero h1{position:absolute;top:290px;width:100%;text-align:center;color:#fff;font-size:58px;font-weight:900;font-style:italic;letter-spacing:1px}
.hero .sub{position:absolute;top:383px;width:100%;text-align:center;color:#fff;font-size:34px;font-weight:400}
.arrow{position:absolute;top:352px;color:#fff;font-size:30px}
.steps{position:absolute;left:115px;top:557px;width:973px;height:223px;display:flex}
.step{flex:1;background:rgba(3,120,170,.88);color:#fff;text-align:center;padding-top:30px}
.step.hot{background:rgba(243,113,34,.95)}
.step svg{width:70px;height:70px}
.step h3{font-size:17px;font-weight:700;margin-top:20px;text-transform:uppercase}
.step p{font-size:12px;line-height:1.6;margin:10px 26px 0}

/* about */
.about{top:780px;height:668px}
.about .ghost{right:-10px;top:10px}
.about h2{position:absolute;left:115px;top:158px;color:var(--blue);font-size:42px;font-weight:900}
.about h2::after{content:"";display:block;width:50px;height:3px;background:var(--orange);margin-top:12px}
.about .copy{position:absolute;left:115px;top:258px;width:480px;font-size:14px;line-height:1.9;color:var(--grey)}
.about .btn{position:absolute;left:115px;top:478px}
.portrait-ring{position:absolute;left:668px;top:150px;width:404px;height:404px;border-radius:50%;border:5px solid var(--orange);padding:8px;border-left-color:var(--blue);border-bottom-color:var(--blue)}
.portrait{width:100%;height:100%;border-radius:50%;background:radial-gradient(circle at 50% 40%,#c99a80,#6b4a3a 75%)}

/* services */
.services{top:1448px;height:599px;background:linear-gradient(180deg,var(--sky),var(--blue))}
.services .ghost{left:0;width:100%;text-align:center;top:100px;color:rgba(255,255,255,.08)}
.services h2{position:absolute;top:118px;width:100%;text-align:center;color:#fff;font-size:44px;font-weight:900}
.services .rule{position:absolute;left:575px;top:178px;margin:0}
.cards{position:absolute;left:115px;top:262px;width:973px;height:225px;display:flex;gap:14px}
.card{flex:1;position:relative}
.card .ph{position:absolute;inset:0;background:linear-gradient(135deg,#d8cbbd,#8e7d70)}
.card .tag{position:absolute;left:0;right:0;background:var(--orange);color:#fff;text-align:center;font-size:15px;font-weight:700;padding:10px 0;text-transform:uppercase}
.card .top{top:0}.card .bot{bottom:0}

/* video */
.video{top:2047px;height:569px;background:var(--pale)}
.video .clip{position:absolute;left:0;top:0;width:598px;height:569px;background:linear-gradient(135deg,#8a5a3c,#3d2a22)}
.play{position:absolute;left:230px;top:215px}
.video .ghost{left:640px;top:20px;font-size:96px}
.video h2{position:absolute;left:648px;top:135px;width:480px;color:var(--blue);font-size:42px;font-weight:900;line-height:1.2}
.video h2::after{content:"";display:block;width:50px;height:3px;background:var(--orange);margin-top:14px}
.video ul{position:absolute;left:648px;top:300px;list-style:none;font-size:14px;color:var(--grey)}
.video li{margin-bottom:16px;padding-left:26px;position:relative}
.video li::before{content:"";position:absolute;left:0;top:3px;width:10px;height:10px;border:2px solid var(--orange);border-radius:50%}
.video .btn{position:absolute;left:648px;top:478px}

/* clients */
.clients{top:2753px;height:127px;display:flex;justify-content:space-around;align-items:center;padding:0 90px}
.client{font-size:18px;font-weight:700;color:var(--blue);display:flex;align-items:center;gap:8px}
.client .mark{width:12px;height:12px;background:var(--blue)}

/* testimonials */
.testi{top:2880px;height:615px}
.testi .ghost{left:0;width:100%;text-align:center;top:70px;font-size:100px}
.testi h2{position:absolute;top:112px;width:100%;text-align:center;color:var(--blue);font-size:44px;font-weight:900}
.testi .rule{position:absolute;left:575px;top:172px;margin:0}
.people{position:absolute;top:262px;left:130px;width:940px;display:flex;justify-content:space-between}
.person{display:flex;align-items:center;gap:16px;width:300px}
.avatar{width:100px;height:100px;border-radius:50%;border:4px solid var(--orange);background:radial-gradient(circle,#c59f86,#5b4436)}
.person h4{color:var(--blue);font-size:18px;font-weight:700}
.person span{display:block;font-size:12px;color:var(--grey);line-height:1.6;margin-top:4px}
.quote{position:absolute;top:412px;left:180px;width:840px;text-align:center;font-size:13.5px;font-style:italic;color:var(--grey);line-height:2}
.dots{position:absolute;top:503px;left:555px;display:flex;gap:8px}
.dots i{width:26px;height:4px;background:#ccc}
.dots i.on{background:var(--orange)}

/* publications */
.press{top:3495px;height:478px;background:linear-gradient(135deg,var(--blue),var(--navy))}
.press .ghost{right:20px;top:320px;color:rgba(255,255,255,.07);font-size:100px}
.press-list{position:absolute;left:90px;top:38px;width:310px;height:414px;background:var(--navy);padding:40px 24px;color:#fff}
.press-list h3{font-size:23px;font-weight:900;text-align:center;text-transform:uppercase;line-height:1.35}
.press-list .rule{margin:14px auto 40px}
.press-list p{font-size:14px;margin-bottom:34px}
.press-list p.on{color:var(--orange)}
.press-list .btn{border-radius:3px;font-size:13px;padding:12px 22px;margin-top:10px}
.covers{position:absolute;left:490px;top:80px;width:600px;height:260px}
.cover{position:absolute}
.press .cap{position:absolute;left:490px;width:600px;text-align:center;top:390px;color:#fff;font-size:17px;font-weight:700}
.press .arrow{top:190px}

/* register */
.register{top:3973px;height:525px;background:#fff}
.register .map{position:absolute;left:60px;top:40px;width:1080px;height:440px;background:radial-gradient(ellipse,#eeeeee,#fff 70%)}
.register h2{position:absolute;top:140px;width:100%;text-align:center;color:var(--blue);font-size:44px;font-weight:900;line-height:1.25}
.register .rule{position:absolute;left:575px;top:262px;margin:0}
.signup{position:absolute;left:298px;top:325px;display:flex;gap:18px}
.signup .field{width:420px;height:50px;border:1px solid #bbb;padding:16px;font-size:13px;color:#999}
.signup .btn{border-radius:3px;height:50px;padding:16px 28px}

/* footer */
.foot{top:4498px;height:277px;background:var(--dark);color:#fff;text-align:center}
.contact{position:absolute;top:46px;width:100%;display:flex;justify-content:center;gap:60px;font-size:14px;align-items:center}
.contact span{display:flex;align-items:center;gap:12px}
.contact svg{width:40px;height:40px}
.foot-nav{position:absolute;top:112px;width:100%;display:flex;justify-content:center;gap:18px;font-size:13px;font-weight:700;text-transform:uppercase}
.foot-nav i{color:var(--orange);font-style:normal}
.copy-line{position:absolute;top:152px;width:100%;font-size:11px;color:#ccc}
.social{position:absolute;top:192px;width:100%;display:flex;justify-content:center;gap:10px}
.social i{width:26px;height:26px;background:var(--sky);border-radius:3px}
</style>
</head>
<body>

<header class="hero">
  <div class="hero-photo" role="img" aria-label="Audience seated in a lecture hall facing a speaker"></div>
  <div class="login">&#128100;&nbsp; CLIENT LOGIN</div>
  <div class="brand">brightwell<b>voicetutor</b></div>
  <nav class="nav"><span class="on">Home</span><span>About</span><span>Clients</span><span>Reviews</span><span>Services</span><span>Contact</span><span>Speaking Secrets</span></nav>
  <span class="arrow" style="left:70px">&#8249;</span><span class="arrow" style="right:70px">&#8250;</span>
  <h1>BRIGHTWELL VOICE TUTOR</h1>
  <div class="sub">Public Speaking Consultant</div>
  <div class="steps">
    <div class="step"><svg viewBox="0 0 70 70" fill="none" stroke="#fff" stroke-width="4"><circle cx="35" cy="35" r="28"/><circle cx="35" cy="35" r="16"/><circle cx="35" cy="35" r="4" fill="#fff"/></svg><h3>The Goal</h3><p>Deliver a focused, engaging message that leads to a successful outcome.</p></div>
    <div class="step hot"><svg viewBox="0 0 70 70" fill="#fff"><rect x="31" y="10" width="8" height="34" rx="3"/><circle cx="35" cy="56" r="5"/></svg><h3>The Challenge</h3><p>Deliver a focused, engaging message that leads to a successful outcome.</p></div>
    <div class="step"><svg viewBox="0 0 70 70" fill="none" stroke="#fff" stroke-width="4"><circle cx="35" cy="35" r="12"/><path d="M35 8v10M35 52v10M8 35h10M52 35h10M16 16l7 7M47 47l7 7M16 54l7-7M47 23l7-7"/></svg><h3>The Solution</h3><p>Deliver a focused, engaging message that leads to a successful outcome.</p></div>
    <div class="step"><svg viewBox="0 0 70 70" fill="none" stroke="#fff" stroke-width="4"><path d="M20 10h30v16a15 15 0 0 1-30 0z"/><path d="M35 41v12M24 60h22M20 16h-8v6a8 8 0 0 0 8 8M50 16h8v6a8 8 0 0 1-8 8"/></svg><h3>The Result</h3><p>Deliver a focused, engaging message that leads to a successful outcome.</p></div>
  </div>
</header>

<section class="about">
  <div class="ghost">ABOUT</div>
  <h2>ABOUT HELENA</h2>
  <p class="copy">Helena Brightwell is an Executive Coach for public speaking and all areas of spoken communication.<br>Helena delivers highly effective communication workshops and individual coaching services to clients in a diverse range of industries. She provides one-on-one support for foreign executives to increase intelligibility in American English and to adapt to American executive culture.</p>
  <span class="btn">Read More</span>
  <div class="portrait-ring"><div class="portrait" role="img" aria-label="Portrait of the speech coach"></div></div>
</section>

<section class="services">
  <div class="ghost">OUR SERVICES</div>
  <h2>OUR SERVICES</h2>
  <div class="rule"></div>
  <div class="cards">
    <div class="card"><div class="ph" role="img" aria-label="Coach working one on one with a client"></div><div class="tag top">Coaching</div></div>
    <div class="card"><div class="ph" role="img" aria-label="Group attending a workshop" style="background:linear-gradient(135deg,#b8b1a8,#5e574f)"></div><div class="tag bot">Custom Workshops</div></div>
    <div class="card"><div class="ph" role="img" aria-label="Business meeting around a table" style="background:linear-gradient(135deg,#e2ddd6,#8d8478)"></div><div class="tag top">Accents</div></div>
    <div class="card"><div class="ph" role="img" aria-label="Audience applauding a keynote speaker" style="background:linear-gradient(135deg,#cdbfb3,#6f5f55)"></div><div class="tag bot">Keynote Speeches</div></div>
  </div>
</section>

<section class="video">
  <div class="clip" role="img" aria-label="Video still of the coach seated on a sofa"></div>
  <svg class="play" width="140" height="140" viewBox="0 0 140 140"><circle cx="70" cy="70" r="64" fill="none" stroke="#fff" stroke-width="6"/><path d="M55 40v60l48-30z" fill="#fff"/></svg>
  <div class="ghost">FREE VIDEO</div>
  <h2>BVT Provides Training, Tools &amp; Techniques</h2>
  <ul>
    <li>Executive Presence – Polishing Personal Presentation Manner</li>
    <li>Addressing and Overcoming Speaking/Communication Anxiety</li>
    <li>Last-Minute Presentation 911</li>
    <li>Media Training</li>
    <li>Modifying Accents for Clarity and Intelligibility</li>
  </ul>
  <span class="btn">Read More</span>
</section>

<section class="clients">
  <span class="client">Northbay Health</span>
  <span class="client"><span class="mark"></span>ClearLens</span>
  <span class="client">Drift Studio</span>
  <span class="client">MKT Partners</span>
  <span class="client"><span class="mark"></span>Onyx Group</span>
  <span class="client">Bluewater Investment Partners</span>
</section>

<section class="testi">
  <div class="ghost">TESTIMONIALS</div>
  <h2>Testimonials</h2>
  <div class="rule"></div>
  <div class="people">
    <div class="person"><div class="avatar" role="img" aria-label="Client portrait"></div><div><h4>Carla Weston</h4><span>CEO, Brightline<br>New York, NY</span></div></div>
    <div class="person"><div class="avatar" role="img" aria-label="Client portrait"></div><div><h4>Nadia Holm</h4><span>Sr. Director,<br>New York, NY</span></div></div>
    <div class="person"><div class="avatar" role="img" aria-label="Client portrait"></div><div><h4>Peter Lund</h4><span>CEO, Brightline<br>New York, NY</span></div></div>
  </div>
  <p class="quote">" I feel like I knocked it out of the park ..... This was my first time working with a professional coach and you made it very comfortable. You understood and took my goals seriously from the start. I feel like I have taken a big step forward on my professional path. Thanks so much! "</p>
  <div class="dots"><i class="on"></i><i></i><i></i></div>
</section>

<section class="press">
  <div class="ghost">PUBLICATIONS</div>
  <div class="press-list">
    <h3>Featured in Recent<br>Publications</h3>
    <div class="rule"></div>
    <p class="on">Spring/Summer 2015 Dapper Style Edition</p>
    <p>Maison Belle Magazine</p>
    <p>Harbor City Post</p>
    <span class="btn">Click to View More</span>
  </div>
  <span class="arrow" style="left:450px">&#8249;</span><span class="arrow" style="right:70px">&#8250;</span>
  <div class="covers">
    <div class="cover" role="img" aria-label="Magazine cover" style="left:0;top:30px;width:150px;height:210px;background:linear-gradient(160deg,#7a2a26,#231616)"></div>
    <div class="cover" role="img" aria-label="Featured magazine cover" style="left:180px;top:0;width:250px;height:260px;background:linear-gradient(160deg,#2f8fd0,#0c2c5a)"></div>
    <div class="cover" role="img" aria-label="Magazine cover" style="left:460px;top:30px;width:150px;height:210px;background:linear-gradient(160deg,#d9d2c4,#6d6a5e)"></div>
  </div>
  <div class="cap">Spring/Summer 2015 Dapper Style Edition</div>
</section>

<section class="register">
  <div class="map" role="img" aria-label="Faint dotted world map"></div>
  <h2>Register and receive FREE "7 Crimes<br>Against Communication</h2>
  <div class="rule"></div>
  <div class="signup"><div class="field">Email Address</div><span class="btn">Register Now</span></div>
</section>

<footer class="foot">
  <div class="contact">
    <span><svg viewBox="0 0 40 40"><circle cx="20" cy="20" r="19" fill="#fff"/><rect x="11" y="13" width="18" height="13" fill="none" stroke="#1e1e1e" stroke-width="2"/><path d="M11 13l9 8 9-8" fill="none" stroke="#1e1e1e" stroke-width="2"/></svg>info@brightwellvoicetutor.com</span>
    <span><svg viewBox="0 0 40 40"><circle cx="20" cy="20" r="19" fill="#fff"/><path d="M14 11c-2 2-2 6 2 11s9 8 11 6l2-2-4-4-2 2c-2-1-4-3-5-5l2-2-4-4z" fill="#1e1e1e"/></svg>555.010.4827</span>
  </div>
  <nav class="foot-nav"><span>Home</span><i>•</i><span>About</span><i>•</i><span>Clients</span><i>•</i><span>Reviews</span><i>•</i><span>Services</span><i>•</i><span>Contact</span><i>•</i><span>Speaking Secrets</span></nav>
  <div class="copy-line">All Rights Reserved . copyright 2019 brightwellvoicetutor.com</div>
  <div class="social"><i></i><i></i><i></i><i></i><i></i></div>
</footer>

</body>
</html>
```